Website Design for a holiday home letting busines

We require a redesign of our present website www.pinebrookstays.com. We want the website to stand out and look professional and clean to make holiday hunters want to book a caravan or lodge holiday with us. Our logo is red however we DO NOT want the website to be red. We want a natural colour scheme.

The final design should communicate that we are a professional company to book with.

On the home page we require;
Overview of company
Photo
Search box for holiday (check in)
Late Deals
Reviews
News

We would like the following pages designed; home page, available dates page, caravans page, content page.

The website should be responsive for smart phones. One website I do like is http://www.verdoliso.be/nl/

Target Market(s)

Families

Industry/Entity Type

Travel

Number of Pages Required

5+ page

Font styles to use
Serif

Requirements
Must have
• The project must be responsive for mobile phones and tablets.
• Ability to search for holiday home holidays
• We want a natural colour scheme.
Nice to have
• A style we like is http://www.verdoliso.be/nl/
Should not have
• Do not use red as a colour for the website. Our logo is red so this is the only time we want this used.

```html
<!DOCTYPE html>
<html lang="en">
<head>
<meta charset="utf-8">
<title>Pinebrook Stays – Caravan &amp; Lodge Holidays</title>
<link href="https://fonts.googleapis.com/css2?family=Open+Sans:wght@400;600;700&display=swap" rel="stylesheet">
<style>
:root{
  --ink:#2f2b24;
  --muted:#6f6a60;
  --line:#d9d4c8;
  --page:#f3f0e8;
  --white:#ffffff;
  --header:#2e2a23;
  --footer:#2a2620;
  --footer-text:#a8a190;
  --accent:#5f7a3a;
  --accent-dark:#4a5f2c;
  --hero:#4a4337;
  --wood:#9a7b55;
  --sky:#a9bcc4;
  --bar:#3a352c;
  --overlay:rgba(20,18,14,.55);
}
*{box-sizing:border-box;margin:0;padding:0}
html,body{width:745px;height:1200px;overflow:hidden}
body{position:relative;font-family:"Open Sans",Arial,sans-serif;color:var(--ink);background:var(--page);font-size:6px;line-height:1.4}
.wrap{position:absolute;left:141px;width:457px}
.site-header{position:absolute;top:0;left:0;width:745px;height:48px;background:var(--header)}
.brand{position:absolute;left:141px;top:9px;display:flex;align-items:center;gap:5px}
.brand-dot{width:18px;height:18px;border-radius:50%;background:var(--accent)}
.brand-name{font-size:11px;font-weight:600;color:var(--white)}
.contact{position:absolute;left:440px;top:9px;color:#cfc8b8;font-size:5.5px;text-align:right;width:100px}
.contact b{display:block;color:var(--white);font-size:6.5px}
.header-icons{position:absolute;left:548px;top:11px;display:flex;gap:4px}
.header-icons span{width:11px;height:11px;border-radius:50%;background:#5a5447}
.nav{position:absolute;top:37px;left:141px;display:flex;gap:16px;color:#c9c2b2;font-size:5px}
.hero{position:absolute;top:48px;left:0;width:745px;height:222px;background:var(--hero)}
.hero-photo{position:absolute;left:330px;top:0;width:415px;height:222px;background:radial-gradient(circle at 55% 55%,#8f7760,#4a4337 70%)}
.hero-text{position:absolute;left:141px;top:70px;width:180px;color:var(--white)}
.hero-text h1{font-size:12px;font-weight:700;margin-bottom:5px;white-space:nowrap}
.hero-text p{font-size:5.5px;color:#e4ddcf}
.hero-btn{display:inline-block;margin-top:10px;padding:3px 9px;border:1px solid #e4ddcf;color:var(--white);font-size:5.5px}
.dots{position:absolute;left:141px;top:190px;display:flex;gap:4px}
.dots i{width:4px;height:4px;border-radius:50%;background:#bdb5a4}
.search{position:absolute;top:270px;left:0;width:745px;height:22px;background:var(--bar)}
.search .wrap{top:4px;display:flex;gap:6px;align-items:center}
.search strong{color:var(--white);font-size:9px;width:45px}
.search .field{flex:1;height:13px;background:var(--white)}
.search .go{width:14px;height:14px}
.section-title{font-size:7px;font-weight:700;color:var(--accent);border-bottom:1px solid var(--line);padding-bottom:2px}
.card-row{display:flex;gap:10px;margin-top:7px}
.card{flex:1;min-width:0}
.card .thumb{height:62px}
.card p{font-size:4.8px;color:var(--muted);margin-top:3px}
.t1{background:linear-gradient(#c9b49b,#8c6d52)}
.t2{background:linear-gradient(var(--sky),#dcdad2)}
.t3{background:linear-gradient(#98adb4,#7b5c3e)}
.t4{background:linear-gradient(#bcc8cc,#eceae4)}
.t5{background:linear-gradient(#8aa372,var(--wood))}
.t6{background:linear-gradient(#7f9a5c,#556b3c)}
.sidebar{position:absolute;left:478px;width:120px;background:var(--white);border:1px solid var(--line)}
.follow{top:468px;height:180px}
.follow h4{background:var(--accent-dark);color:var(--white);font-size:5.5px;padding:3px 5px}
.post{display:flex;gap:4px;padding:4px 5px;border-bottom:1px solid #ece8de}
.post i{width:14px;height:14px;background:#9aa88a;flex:none}
.post span{font-size:4.5px;color:var(--muted)}
.calendar{top:652px;height:75px;padding:4px}
.calendar h5{font-size:5.5px;margin-bottom:3px;color:var(--accent-dark)}
.calendar table{width:100%;border-collapse:collapse;font-size:4.5px;text-align:center;color:var(--muted)}
.calendar td{padding:1px}
.review{position:absolute;top:765px;left:0;width:745px;height:90px;background:var(--white)}
.review h3{text-align:center;font-size:7px;color:var(--accent);margin-top:6px}
.avatar{position:absolute;left:205px;top:24px;width:30px;height:34px;background:linear-gradient(#cfc6bb,#8e8478)}
.review p{position:absolute;left:270px;top:26px;width:270px;font-size:5px;color:var(--muted)}
.blog{top:873px}
.blog-row{display:flex;gap:15px;margin-top:8px}
.blog-row article{flex:1}
.blog-row .thumb{height:76px}
.blog-row h4{font-size:6px;margin:4px 0 2px;color:var(--accent-dark)}
.blog-row p{font-size:4.8px;color:var(--muted)}
.more{display:inline-block;margin-top:3px;padding:1px 5px;border:1px solid var(--line);font-size:4.5px}
.newsletter{position:absolute;top:1055px;left:0;width:745px;height:26px;background:var(--bar)}
.newsletter .wrap{top:7px;display:flex;gap:6px;align-items:center;color:var(--white);font-size:6px}
.newsletter .field{width:70px;height:11px;background:var(--white)}
.newsletter .btn{padding:2px 6px;background:var(--accent-dark);font-size:5px}
.site-footer{position:absolute;top:1081px;left:0;width:745px;height:119px;background:var(--footer);color:var(--footer-text);font-size:4.8px}
.cols{position:absolute;left:141px;top:10px;display:flex;gap:22px}
.cols div{width:95px}
.cols h6{color:var(--white);font-size:5.5px;margin-bottom:3px}
.social{position:absolute;left:500px;top:30px;display:flex;gap:4px}
.social span{width:10px;height:10px;border-radius:50%;background:#6f7f5a}
.copy{position:absolute;left:141px;top:98px}
.overlay{position:absolute;inset:0;background:var(--overlay)}
.modal{position:absolute;left:248px;top:55px;width:255px;height:193px;background:var(--white);border:4px solid #eee}
.modal-photo{height:102px;background:linear-gradient(#d8e4e4,#f0e9df)}
.modal h2{font-size:6px;text-align:center;font-weight:600;margin-top:12px}
.modal p{font-size:4.8px;text-align:center;color:var(--muted)}
.modal form{display:flex;gap:6px;margin:16px 12px 0}
.modal .field{flex:1;height:11px;border:1px solid var(--line);font-size:4.5px;color:#aaa;padding:2px}
.modal .send{padding:2px 7px;background:var(--bar);color:var(--white);font-size:5px}
.close{position:absolute;right:-8px;top:-8px;width:12px;height:12px;border-radius:50%;background:var(--white);border:1px solid #999}
</style>
</head>
<body>
<header class="site-header">
  <div class="brand"><span class="brand-dot"></span><span class="brand-name">Pinebrook Stays</span></div>
  <div class="contact"><b>01632 960 418</b>stay@pinebrookstays.com</div>
  <div class="header-icons"><span></span><span></span><span></span></div>
  <nav class="nav"><span>Home</span><span>Caravans</span><span>Lodges</span><span>Available Dates</span><span>Late Deals</span><span>Reviews</span><span>News</span><span>Contact</span></nav>
</header>

<section class="hero">
  <div class="hero-photo" role="img" aria-label="Photo of a family enjoying a lodge holiday"></div>
  <div class="hero-text">
    <h1>Private Holiday Homes</h1>
    <p>Relaxing caravan and lodge breaks for the whole family in quiet countryside parks across the region.</p>
    <span class="hero-btn">Read more</span>
  </div>
  <div class="dots"><i></i><i></i><i></i><i></i></div>
</section>

<section class="search">
  <div class="wrap"><strong>Search</strong><span class="field"></span><span class="field"></span><span class="field"></span><span class="field"></span><span class="field"></span>
    <svg class="go" viewBox="0 0 14 14"><circle cx="6" cy="6" r="4" fill="none" stroke="#fff" stroke-width="1.5"/><line x1="9" y1="9" x2="12.5" y2="12.5" stroke="#fff" stroke-width="1.5"/></svg>
  </div>
</section>

<section class="wrap" style="top:306px">
  <h3 class="section-title">Late Deals</h3>
  <div class="card-row">
    <div class="card"><div class="thumb t1" role="img" aria-label="Lodge interior photo"></div><p>Cosy lodge, sleeps four, from £249</p></div>
    <div class="card"><div class="thumb t2" role="img" aria-label="Static caravan photo"></div><p>Family caravan, sleeps six, from £199</p></div>
    <div class="card"><div class="thumb t3" role="img" aria-label="Wooden lodge photo"></div><p>Forest lodge with hot tub, from £329</p></div>
    <div class="card"><div class="thumb t4" role="img" aria-label="Caravan on a park photo"></div><p>Seaside caravan, short break, £179</p></div>
    <div class="card"><div class="thumb t5" role="img" aria-label="Timber lodge photo"></div><p>Lakeside lodge, weekend, from £289</p></div>
  </div>
</section>

<section class="wrap" style="top:466px;width:325px">
  <h3 class="section-title">Our Caravans</h3>
  <div class="card-row">
    <div class="card"><div class="thumb t2" role="img" aria-label="Caravan photo"></div><p>Willow caravan, two bedrooms, decking</p></div>
    <div class="card"><div class="thumb t4" role="img" aria-label="Caravan photo"></div><p>Meadow caravan, three bedrooms, view</p></div>
    <div class="card"><div class="thumb t6" role="img" aria-label="Caravan on grass photo"></div><p>Orchard caravan, pet friendly, garden</p></div>
  </div>
</section>

<section class="wrap" style="top:603px;width:325px">
  <h3 class="section-title">Our Lodges</h3>
  <div class="card-row">
    <div class="card"><div class="thumb t1" role="img" aria-label="Lodge lounge photo"></div><p>Birch lodge, open plan, log burner</p></div>
    <div class="card"><div class="thumb t5" role="img" aria-label="Lodge exterior photo"></div><p>Cedar lodge, private hot tub, veranda</p></div>
    <div class="card"><div class="thumb t6" role="img" aria-label="Woodland path photo"></div><p>Oak lodge, woodland walks nearby</p></div>
  </div>
</section>

<aside class="sidebar follow">
  <h4>Follow Us</h4>
  <div class="post"><i></i><span>New lodges open this spring on the lakeside park.</span></div>
  <div class="post"><i></i><span>Thank you to all our families for lovely reviews.</span></div>
  <div class="post"><i></i><span>Half term breaks still available, book now.</span></div>
  <div class="post"><i></i><span>Our caravans now welcome well behaved dogs.</span></div>
  <div class="post"><i></i><span>Photos from a sunny week at the woodland park.</span></div>
</aside>
<aside class="sidebar calendar">
  <h5>Available Dates</h5>
  <table>
    <tr><td>M</td><td>T</td><td>W</td><td>T</td><td>F</td><td>S</td><td>S</td></tr>
    <tr><td>1</td><td>2</td><td>3</td><td>4</td><td>5</td><td>6</td><td>7</td></tr>
    <tr><td>8</td><td>9</td><td>10</td><td>11</td><td>12</td><td>13</td><td>14</td></tr>
    <tr><td>15</td><td>16</td><td>17</td><td>18</td><td>19</td><td>20</td><td>21</td></tr>
    <tr><td>22</td><td>23</td><td>24</td><td>25</td><td>26</td><td>27</td><td>28</td></tr>
  </table>
</aside>

<section class="review">
  <h3>Latest Review</h3>
  <div class="avatar" role="img" aria-label="Portrait of a guest reviewer"></div>
  <p>“We had a wonderful week in our lodge. The park was peaceful, the children loved the woodland trails and everything was spotless on arrival. Booking was simple and the team were friendly and helpful throughout. We will certainly be returning next summer.” — The Harper family</p>
</section>

<section class="wrap blog">
  <h3 class="section-title">Blog</h3>
  <div class="blog-row">
    <article><div class="thumb t4" role="img" aria-label="Bright caravan interior photo"></div><h4>Our newly refurbished caravans</h4><p>Fresh kitchens, new beds and modern bathrooms are now ready in all our family caravans for this season.</p><span class="more">Read more</span></article>
    <article><div class="thumb t5" role="img" aria-label="Lodge among trees photo"></div><h4>Autumn breaks in the woods</h4><p>Crisp walks, warm log burners and quiet evenings make autumn a lovely time for a lodge holiday.</p><span class="more">Read more</span></article>
  </div>
</section>

<section class="newsletter"><div class="wrap">Newsletter Subscribe <span class="field"></span><span class="field"></span><span class="btn">Subscribe</span></div></section>

<footer class="site-footer">
  <div class="cols">
    <div><h6>About Us</h6>Family run holiday homes in calm countryside parks.</div>
    <div><h6>Useful Links</h6>Caravans<br>Lodges<br>Late Deals<br>Contact</div>
    <div><h6>Contact</h6>01632 960 418<br>stay@pinebrookstays.com<br>www.pinebrookstays.com</div>
  </div>
  <div class="social"><span></span><span></span><span></span><span></span><span></span></div>
  <div class="copy">© Pinebrook Stays. All rights reserved.</div>
</footer>

<div class="overlay"></div>
<div class="modal">
  <span class="close"></span>
  <div class="modal-photo" role="img" aria-label="Photo of a smiling family together"></div>
  <h2>Request a brochure and receive our latest offers</h2>
  <p>Enter your details below to hear about late deals first.</p>
  <form><span class="field">Name</span><span class="field">Email</span><span class="send">Submit</span></form>
</div>
</body>
</html>
```